Young company in the agrifood product sector *

Our company% 26 # 233; t% 26 # 233; Ambrel Crest low% 26 # 233; % 26 # 224; Toulouse et sp% 26 # 233; cialis% 26 # 233; in the packaging and marketing of beehive products, We need a design of% 26 # 39;% 26 # 39;% 26 # 233; label for honey jar of 250g, The% 26 # 233; labels destiny% 26 # 233; the honey jars will be transparent so that the nectar is visible from the front, our Ambrel Crest logo must be% 26 # 234; be located% 26 # 233; above / middle of% 26 # 393% label followed below the appellation, for example Ch% 26 # 226; taignier followed below the country of% 26 # 39; origin France tracking below r% 26 # 233; region of r% 26 # 233; colte Midi-Pyr% 26 # 233; n% 26 # 233; es and below l% 26 # 39;% 26 # 233; label weight 250g and% 26lt;% 26lt;% 26lt; Honey% 26gt;% 26gt; on the% 26 # 39;% 26 # 233; label will be a plus but optional, The dimensions of the% 26 # 39;% 26 # 233; label are the following 6cm x 6cm. The design must inspire quality% 26 # 233; luxury, l% 26 # 39;% 26 # 233; l% 26 # 233; elegance and confidence, these are quality honey% 26 # 233; and rare honeys from around the world which are very expensive. Very important, the honeys have different colors, this can range from white to orange yellow or darker shades of brown% 26 # 234; black, that's why we would like to have at least 3 colors for light honey, medium dark% 26 # 233; and dark% 26 # 233 ;, Regarding the colors you have free choice of course% 26 # 251; r taking into account the colors of the honey which must% 26 # 234; be visible% 26 # 224; through the% 26 # 39;% 26 # 233; transparent label You will find attached the files of our Ambrel Crest logo. 20%% 26 # 224; 40% transparency on the% 26 # 39;% 26 # 233; label would be reasonable but% 26 # 224; you to see which is better, thanks
- Krone one

```html
<!DOCTYPE html>
<html lang="fr">
<head>
<meta charset="utf-8">
<title>Ambrel Crest – Châtaignier honey labels</title>
<link rel="stylesheet" href="https://fonts.googleapis.com/css2?family=Quicksand:wght@600;700&family=Barlow+Condensed:wght@600&display=swap">
<style>
  :root {
    --backdrop: #eef0f1;
    --honey-light-top: #ffd46a;
    --honey-light-bottom: #f3a91c;
    --honey-dark-top: #ff9a1c;
    --honey-dark-bottom: #d8420a;
    --ink-black: #0d0b08;
    --gold-text: #f4c24c;
    --silver-light: #f4f2ee;
    --silver-mid: #c9c6c0;
    --silver-dark: #a9a59e;
    --orange-text: #ef7a1e;
    --logo-black: #1a1510;
    --logo-silver: #e9e5de;
  }
  html, body {
    margin: 0;
    width: 1200px;
    height: 923px;
    overflow: hidden;
    background: var(--backdrop);
  }
  .canvas {
    position: relative;
    width: 1200px;
    height: 923px;
  }
  .label {
    position: absolute;
    top: 215px;
    width: 310px;
    height: 500px;
    border-radius: 28px;
    overflow: hidden;
  }
  .label--light {
    left: 225px;
    background: linear-gradient(180deg, var(--honey-light-top), var(--honey-light-bottom));
  }
  .label--dark {
    left: 630px;
    background: linear-gradient(180deg, var(--honey-dark-top) 0%, #f47a10 60%, var(--honey-dark-bottom) 100%);
  }
  .label svg { display: block; }
  .brand {
    font-family: "Barlow Condensed", sans-serif;
    font-weight: 600;
    font-size: 34px;
  }
  .variety {
    font-family: "Quicksand", sans-serif;
    font-weight: 700;
    font-size: 29px;
  }
  .country {
    font-family: "Quicksand", sans-serif;
    font-weight: 700;
    font-size: 23px;
    letter-spacing: 2px;
  }
  .region {
    font-family: "Quicksand", sans-serif;
    font-weight: 700;
    font-size: 12px;
  }
  .weight {
    font-family: "Quicksand", sans-serif;
    font-weight: 700;
    font-size: 14px;
  }
</style>
</head>
<body>
<main class="canvas">

  <section class="label label--light" aria-label="Châtaignier label, black edition">
    <svg width="310" height="500" viewBox="0 0 310 500">
      <g class="brand-block" fill="var(--logo-black)">
        <circle cx="104" cy="108" r="11"/>
        <text class="brand" x="124" y="120">Ambrel</text>
        <text class="brand" x="124" y="152">Crest</text>
      </g>
      <path class="band band--variety" fill="var(--ink-black)" d="M37 250 V214 C37 190 90 183 155 183 C220 183 273 190 273 214 V250 Z"/>
      <text class="variety" x="155" y="228" text-anchor="middle" fill="var(--gold-text)">Châtaignier</text>
      <path class="band band--country" fill="var(--ink-black)" d="M40 276 H270 L252 317 H58 Z"/>
      <text class="country" x="155" y="305" text-anchor="middle" fill="var(--gold-text)">FRANCE</text>
      <path class="band band--region" fill="var(--ink-black)" d="M72 344 H238 L224 371 H86 Z"/>
      <text class="region" x="155" y="362" text-anchor="middle" fill="var(--gold-text)">Midi-Pyrénées</text>
      <path class="pointer" fill="var(--ink-black)" d="M121 400 H189 L155 433 Z"/>
      <text class="weight" x="155" y="458" text-anchor="middle" fill="var(--ink-black)">250g</text>
    </svg>
  </section>

  <section class="label label--dark" aria-label="Châtaignier label, silver edition">
    <svg width="310" height="500" viewBox="0 0 310 500">
      <defs>
        <linearGradient id="silver-foil" x1="0" y1="0" x2="1" y2="0">
          <stop offset="0" stop-color="var(--silver-dark)"/>
          <stop offset="0.45" stop-color="var(--silver-light)"/>
          <stop offset="1" stop-color="var(--silver-mid)"/>
        </linearGradient>
      </defs>
      <g class="brand-block" fill="var(--logo-silver)">
        <circle cx="104" cy="108" r="11"/>
        <text class="brand" x="124" y="120">Ambrel</text>
        <text class="brand" x="124" y="152">Crest</text>
      </g>
      <path class="band band--variety" fill="url(#silver-foil)" d="M37 250 V214 C37 190 90 183 155 183 C220 183 273 190 273 214 V250 Z"/>
      <text class="variety" x="155" y="228" text-anchor="middle" fill="var(--orange-text)">Châtaignier</text>
      <path class="band band--country" fill="url(#silver-foil)" d="M40 276 H270 L252 317 H58 Z"/>
      <text class="country" x="155" y="305" text-anchor="middle" fill="var(--orange-text)">FRANCE</text>
      <path class="band band--region" fill="url(#silver-foil)" d="M72 344 H238 L224 371 H86 Z"/>
      <text class="region" x="155" y="362" text-anchor="middle" fill="var(--orange-text)">Midi-Pyrénées</text>
      <path class="pointer" fill="url(#silver-foil)" d="M121 400 H189 L155 433 Z"/>
      <text class="weight" x="155" y="458" text-anchor="middle" fill="var(--silver-light)">250g</text>
    </svg>
  </section>

</main>
</body>
</html>
```